VORTEQ

It’s is a startup business. We design and build new products.

Target Market(s)

For my first two products, they are targeting the laundry market, hanger accessory, and new modern style clothes dryer. I also have a Pet Treat product at patent stage, and there are other products not yet started but will be more engineering based. Therefore from young adults to older population

Industry/Entity Type

Colours of website to match the logo (att)

Coding

Coded - Design and coding required

Number of Pages Required

1 page

Font styles to use
Other font styles liked:
• Some of the same font as the logo

Colors

Designer to choose colors to be used in the design.

Requirements
Must have
• An upbeat vibe - the logo looks great so inline with that !
Should not have
• anything old fashioned and old style fonts

```html
<!DOCTYPE html>
<html lang="en">
<head>
<meta charset="utf-8">
<title>VORTEQ – Innovating Everyday Solutions</title>
<link href="https://fonts.googleapis.com/css2?family=Michroma&family=Montserrat:wght@400;500;600;700&display=swap" rel="stylesheet">
<style>
:root{
  --navy:#0b1838;
  --navy-2:#142a5c;
  --blue:#1b6fb8;
  --blue-bright:#1a9ad8;
  --indigo:#2c3f94;
  --teal:#5fd3d2;
  --teal-deep:#20c0cc;
  --ink:#1b1b1f;
  --text:#3a3a40;
  --header-bg:#f1f0ef;
  --about-bg:#d6ecf6;
  --footer-bg:#3b3b3e;
  --white:#ffffff;
}
*{margin:0;padding:0;box-sizing:border-box}
html,body{width:1200px;height:3607px;overflow:hidden;background:var(--white)}
body{font-family:'Montserrat',sans-serif;color:var(--text);position:relative}
.page{position:relative;width:1200px;height:3607px;overflow:hidden}
.abs{position:absolute}
.display{font-family:'Michroma',sans-serif;text-transform:uppercase;letter-spacing:3px}

/* header */
.site-header{position:absolute;top:0;left:0;width:1200px;height:84px;background:var(--header-bg)}
.brand{position:absolute;display:flex;align-items:center;gap:10px;font-family:'Montserrat',sans-serif;font-weight:700;letter-spacing:4px;color:var(--blue)}
.brand-dot{width:14px;height:14px;border-radius:50%;background:var(--teal-deep)}
.site-header .brand{left:118px;top:24px;font-size:30px}
.nav{position:absolute;top:33px;left:0;font-size:14px;font-weight:500;color:#2b2b33}
.nav a{position:absolute;white-space:nowrap;text-decoration:none;color:inherit}
.nav a.active{color:var(--blue);font-weight:700}
.btn{position:absolute;display:flex;align-items:center;justify-content:center;border-radius:30px;font-size:15px;font-weight:600;text-transform:uppercase;text-decoration:none;letter-spacing:.3px}
.btn-contact{left:916px;top:20px;width:171px;height:46px;background:linear-gradient(90deg,#1780c1,#1b5ea6);color:var(--white)}

/* hero */
.hero{position:absolute;top:84px;left:0;width:1200px;height:600px}
.hero-bg{position:absolute;inset:0}
.hero-title{position:absolute;left:112px;top:190px;color:var(--white);font-size:21px;line-height:38px;letter-spacing:3px}
.hero-copy{position:absolute;left:111px;top:310px;width:490px;color:#e8eefa;font-size:16px;line-height:30px}
.btn-start{left:111px;top:416px;width:170px;height:46px;background:var(--teal);color:#13334a;font-size:15px}

/* section titles */
.section-title{position:absolute;left:0;width:1200px;text-align:center;font-size:23px;color:var(--ink)}
.section-title .accent{color:var(--blue-bright)}

/* carousel arrows */
.arrow{position:absolute;width:44px;height:44px}

/* service cards */
.service-card{position:absolute;top:844px;width:297px;height:279px;background:var(--white);box-shadow:0 4px 10px rgba(0,0,0,.18)}
.service-card .media{position:absolute;left:4px;top:2px;width:289px;height:191px}
.service-card h3{position:absolute;left:15px;top:206px;font-size:17px;font-weight:500;line-height:29px;color:var(--ink)}
.service-card svg.icon{position:absolute;right:18px;top:208px}

/* about */
.about{position:absolute;top:1211px;left:0;width:1200px;height:617px;background:var(--about-bg)}
.about .media{position:absolute}
.logo-tile{position:absolute;left:357px;top:385px;width:231px;height:116px;background:#3a3a3d;display:flex;align-items:center;justify-content:center}
.logo-tile .brand{position:static;font-size:26px;color:var(--teal)}
.about-title{position:absolute;left:672px;top:104px;font-size:23px;color:var(--ink)}
.about-title .accent{color:var(--blue-bright)}
.about-copy{position:absolute;left:626px;top:151px;width:410px;font-size:14px;line-height:28.3px;color:#333}
.btn-read{left:629px;top:438px;width:171px;height:48px;background:linear-gradient(90deg,#1f8ad0,#2a4a9c);color:var(--white)}

/* resources */
.resources{position:absolute;top:1827px;left:0;width:1200px;height:415px}
.resources-title{position:absolute;left:0;width:1200px;top:94px;text-align:center;font-size:23px;color:var(--white)}
.resources-copy{position:absolute;left:238px;top:140px;width:724px;text-align:center;color:var(--white);font-size:14px;line-height:28.3px}
.btn-res{left:511px;top:284px;width:171px;height:48px;background:var(--teal);color:#13334a}

/* process */
.step{position:absolute;top:2380px;width:150px;text-align:center}
.step-label{position:absolute;top:2505px;width:200px;text-align:center;font-size:17px;font-weight:500;color:var(--ink)}

/* blogs */
.blog-card{position:absolute;top:2691px;width:287px;height:420px;background:var(--white);box-shadow:0 3px 10px rgba(0,0,0,.12)}
.blog-card .media{position:absolute;left:0;top:0;width:287px;height:218px}
.blog-date{position:absolute;left:17px;top:201px;padding:0 16px;height:36px;line-height:36px;border-radius:18px;background:var(--indigo);color:var(--white);font-size:15px;font-weight:600}
.blog-card h3{position:absolute;left:17px;top:249px;width:250px;font-size:19px;font-weight:500;line-height:30px;color:var(--ink)}
.blog-rule{position:absolute;left:17px;top:318px;width:80px;height:3px;background:var(--teal-deep)}
.blog-card p{position:absolute;left:21px;top:345px;width:240px;font-size:14px;line-height:26px;color:#444}

/* footer */
.site-footer{position:absolute;top:3200px;left:0;width:1200px;height:407px;background:var(--footer-bg);color:var(--white)}
.site-footer .brand{left:115px;top:77px;font-size:27px;color:var(--teal)}
.footer-col{position:absolute;top:80px}
.footer-col h4{font-size:19px;font-weight:600;letter-spacing:.5px;margin-bottom:20px}
.footer-col ul{list-style:none}
.footer-col li{font-size:15px;line-height:32px;color:#eee}
.newsletter-note{font-size:12.5px;line-height:22px;color:#eee;width:190px}
.newsletter-field{position:absolute;left:864px;top:199px;width:216px;height:42px;border-radius:21px;background:var(--white);color:#666;font-size:13px;padding-left:14px;line-height:42px}
.newsletter-field svg{position:absolute;right:14px;top:10px}
.footer-rule{position:absolute;left:115px;top:328px;width:977px;height:1px;background:#6a6a6e}
.copyright{position:absolute;left:0;width:1200px;top:356px;text-align:center;font-size:14px;color:#eee}
</style>
</head>
<body>
<div class="page">

  <!-- Header -->
  <header class="site-header">
    <div class="brand"><span class="brand-dot"></span>VORTEQ</div>
    <nav class="nav">
      <a class="active" style="left:465px">HOME</a>
      <a style="left:542px">ABOUT US</a>
      <a style="left:647px">WHY CHOOSE US</a>
      <a style="left:802px">SERVICES</a>
    </nav>
    <a class="btn btn-contact">Contact Us</a>
  </header>

  <!-- Hero -->
  <section class="hero">
    <svg class="hero-bg" width="1200" height="600" viewBox="0 0 1200 600" role="img" aria-label="Glowing light bulb resting on an open hand with connected technology icons">
      <defs>
        <linearGradient id="heroGrad" x1="0" y1="0" x2="1" y2="0.4">
          <stop offset="0" stop-color="#101a38"/>
          <stop offset="0.5" stop-color="#17295a"/>
          <stop offset="0.75" stop-color="#2a2a55"/>
          <stop offset="1" stop-color="#1a1e3c"/>
        </linearGradient>
        <radialGradient id="bulbGlow" cx="0.78" cy="0.35" r="0.28">
          <stop offset="0" stop-color="#ffb347" stop-opacity=".85"/>
          <stop offset="0.5" stop-color="#c04a6a" stop-opacity=".35"/>
          <stop offset="1" stop-color="#1a1e3c" stop-opacity="0"/>
        </radialGradient>
      </defs>
      <path d="M0 0H1200V508C1120 520 1010 540 910 553C800 567 705 575 600 588C500 575 400 566 300 555C170 540 80 520 0 480Z" fill="url(#heroGrad)"/>
      <path d="M0 0H1200V508C1120 520 1010 540 910 553C800 567 705 575 600 588C500 575 400 566 300 555C170 540 80 520 0 480Z" fill="url(#bulbGlow)"/>
    </svg>
    <svg class="abs" style="left:588px;top:554px" width="24" height="34" viewBox="0 0 24 34">
      <rect x="2" y="2" width="20" height="30" rx="10" fill="none" stroke="#fff" stroke-width="2.5"/>
      <line x1="12" y1="9" x2="12" y2="15" stroke="#fff" stroke-width="2.5" stroke-linecap="round"/>
    </svg>
    <h1 class="hero-title display">Innovating Everyday<br>Solutions — Designed<br>for Modern Living</h1>
    <p class="hero-copy">Vorteq is a startup dedicated to designing and building innovative products that simplify life – from laundry solutions to pet care and beyond.</p>
    <a class="btn btn-start">Get Started</a>
  </section>

  <!-- Services -->
  <h2 class="section-title display" style="top:768px">Discover Our <span class="accent">Services</span></h2>

  <svg class="arrow" style="left:29px;top:947px" viewBox="0 0 44 44"><circle cx="22" cy="22" r="20" fill="#fff" stroke="#b9b9b9" stroke-width="2"/><path d="M25 13L16 22L25 31" fill="none" stroke="#b9b9b9" stroke-width="2.5"/></svg>
  <svg class="arrow" style="left:1119px;top:947px" viewBox="0 0 44 44"><circle cx="22" cy="22" r="20" fill="#fff" stroke="#1b6fb8" stroke-width="2.5"/><path d="M19 13L28 22L19 31" fill="none" stroke="#1b6fb8" stroke-width="2.5"/></svg>

  <article class="service-card" style="left:112px">
    <div class="media" role="img" aria-label="Engineer working on a 3D product model at a computer" style="background:linear-gradient(135deg,#cfd6dc,#7f8a94 55%,#3d4a57)"></div>
    <h3>Product Design &amp;<br>Development</h3>
    <svg class="icon" width="54" height="50" viewBox="0 0 54 50" fill="none" stroke="#1a9ad8" stroke-width="2"><rect x="3" y="8" width="48" height="36" rx="3"/><line x1="3" y1="16" x2="51" y2="16"/><path d="M27 22L36 27V36L27 41L18 36V27Z"/><path d="M18 27L27 32L36 27M27 32V41"/></svg>
  </article>
  <article class="service-card" style="left:451px">
    <div class="media" role="img" aria-label="Modern front-loading washing machine in a tech-lit room" style="background:linear-gradient(135deg,#1d2f48,#6f9ab9 55%,#b8d3e3)"></div>
    <h3>Innovative Laundry<br>Solutions</h3>
    <svg class="icon" width="54" height="50" viewBox="0 0 54 50" fill="none" stroke="#1b6fb8" stroke-width="2.4"><rect x="3" y="4" width="36" height="42" rx="5"/><line x1="3" y1="14" x2="39" y2="14"/><circle cx="21" cy="30" r="10"/><path d="M44 14a6 6 0 0 1 0 8M48 10a11 11 0 0 1 0 16"/><rect x="42" y="32" width="10" height="12" rx="2"/></svg>
  </article>
  <article class="service-card" style="left:791px">
    <div class="media" role="img" aria-label="Digital blue wireframe of a dog" style="background:linear-gradient(135deg,#0e2a52,#2e74b6 50%,#8fc4e8)"></div>
    <h3>Pet Care<br>Innovation</h3>
    <svg class="icon" width="54" height="50" viewBox="0 0 54 50" fill="none" stroke="#1b6fb8" stroke-width="2.2"><path d="M6 22C6 34 14 44 27 44S48 34 48 22"/><path d="M12 26C12 34 18 40 27 40S42 34 42 26"/><circle cx="27" cy="26" r="5"/><circle cx="20" cy="17" r="2.5"/><circle cx="27" cy="13" r="2.5"/><circle cx="34" cy="17" r="2.5"/></svg>
  </article>

  <!-- About -->
  <section class="about">
    <div class="media" role="img" aria-label="Row of washing machines in a laundromat" style="left:112px;top:91px;width:231px;height:196px;background:linear-gradient(135deg,#9aa3ad,#d9dee3 60%,#8c96a0)"></div>
    <div class="media" role="img" aria-label="Teal jacket hanging on a hanger" style="left:357px;top:91px;width:231px;height:277px;background:linear-gradient(160deg,#7aa3b3,#1e6e8c 50%,#2b4e63)"></div>
    <div class="media" role="img" aria-label="Veterinarian greeting a happy dog" style="left:112px;top:301px;width:231px;height:196px;background:linear-gradient(135deg,#dfe6ea,#b08454 55%,#4a6a90)"></div>
    <div class="logo-tile"><div class="brand"><span class="brand-dot"></span>VORTEQ</div></div>
    <h2 class="about-title display"><span class="accent">About</span> Us</h2>
    <p class="about-copy">Lorem Ipsum is simply dummy text of the printing and typesetting industry. Lorem Ipsum has been the industry's standard dummy text ever since the 1500s, when an unknown printer took a galley of type and scrambled it to make a type specimen book. It has survived not only five centuries, but also the leap into electronic typesetting, remaining essentially unchanged.<br>It was popularised in the 1960s with the release of Letraset sheets containing Lorem Ipsum passages,</p>
    <a class="btn btn-read">Read More</a>
  </section>

  <!-- Resources -->
  <section class="resources">
    <svg class="abs" style="left:0;top:0" width="1200" height="415" viewBox="0 0 1200 415" role="img" aria-label="Silhouettes of a team meeting in a blue tinted office">
      <defs>
        <linearGradient id="resGrad" x1="0" y1="0" x2="0" y2="1">
          <stop offset="0" stop-color="#23c4cf"/>
          <stop offset="0.45" stop-color="#2a7ec0"/>
          <stop offset="1" stop-color="#2d3f95"/>
        </linearGradient>
      </defs>
      <path d="M0 0H1200V315C1000 385 800 413 600 413S200 385 0 315Z" fill="url(#resGrad)"/>
    </svg>
    <h2 class="resources-title display">Our Resources</h2>
    <p class="resources-copy">Lorem Ipsum is simply dummy text of the printing and typesetting industry. Lorem Ipsum has been the industry's standard dummy text ever since the 1500s, when an unknown printer took a galley of type and scrambled it to make a type specimen book. It has survived not only five centuries, but also the leap into electronic typesetting, remaining essentially unchanged.</p>
    <a class="btn btn-res">Read More</a>
  </section>

  <!-- How we work -->
  <h2 class="section-title display" style="top:2300px">How We <span class="accent">Work</span></h2>

  <svg class="abs" style="left:0;top:2370px" width="1200" height="130" viewBox="0 0 1200 130">
    <defs>
      <g id="stepRing">
        <circle r="56" fill="#fff" stroke="#2c3f94" stroke-width="2" stroke-dasharray="7 5"/>
        <circle r="45" fill="#2c3f94"/>
      </g>
      <path id="link" d="M0 0C20 18 55 18 90 -4" fill="none" stroke="#9a9a9a" stroke-width="2.5"/>
    </defs>
    <g fill="none" stroke="#9a9a9a" stroke-width="2.5">
      <path d="M258 86C282 104 318 104 346 80M338 78l9 1l-4 9"/>
      <path d="M454 86C478 104 514 104 542 80M534 78l9 1l-4 9"/>
      <path d="M650 86C674 104 710 104 738 80M730 78l9 1l-4 9"/>
      <path d="M846 86C870 104 906 104 934 80M926 78l9 1l-4 9"/>
    </g>
    <use href="#stepRing" x="206" y="66"/>
    <use href="#stepRing" x="402" y="66"/>
    <use href="#stepRing" x="597" y="66"/>
    <use href="#stepRing" x="793" y="66"/>
    <use href="#stepRing" x="989" y="66"/>
    <g fill="none" stroke="#fff" stroke-width="2.4" stroke-linecap="round">
      <circle cx="203" cy="63" r="12"/><line x1="212" y1="72" x2="222" y2="82"/><circle cx="203" cy="63" r="5"/>
      <circle cx="402" cy="58" r="12"/><path d="M396 58h12M402 52v12"/><path d="M386 84l10-12M418 84l-10-12"/>
      <circle cx="605" cy="55" r="8"/><path d="M582 70l10-6 10 6v12l-10 6-10-6Z"/><circle cx="612" cy="78" r="6"/>
      <rect x="779" y="46" width="28" height="38" rx="2"/><path d="M785 58h16M785 66h16M785 74h10"/>
      <circle cx="989" cy="58" r="10"/><circle cx="989" cy="58" r="4"/><rect x="970" y="76" width="38" height="8" rx="4"/>
    </g>
    <g font-family="Montserrat, sans-serif" font-weight="700" font-size="28" fill="#fff" text-anchor="middle">
      <circle cx="166" cy="28" r="26" fill="#23c4cf"/><text x="166" y="38">01</text>
      <circle cx="362" cy="28" r="26" fill="#23c4cf"/><text x="362" y="38">02</text>
      <circle cx="557" cy="28" r="26" fill="#23c4cf"/><text x="557" y="38">03</text>
      <circle cx="753" cy="28" r="26" fill="#23c4cf"/><text x="753" y="38">04</text>
      <circle cx="949" cy="28" r="26" fill="#23c4cf"/><text x="949" y="38">05</text>
    </g>
  </svg>
  <div class="step-label" style="left:106px">Research</div>
  <div class="step-label" style="left:302px">Design</div>
  <div class="step-label" style="left:497px">Prototyping</div>
  <div class="step-label" style="left:693px">Testing</div>
  <div class="step-label" style="left:889px">Production</div>

  <!-- Blogs -->
  <h2 class="section-title display" style="top:2612px">Our <span class="accent">Blogs</span></h2>

  <svg class="arrow" style="left:29px;top:2846px" viewBox="0 0 44 44"><circle cx="22" cy="22" r="20" fill="#fff" stroke="#b9b9b9" stroke-width="2"/><path d="M25 13L16 22L25 31" fill="none" stroke="#b9b9b9" stroke-width="2.5"/></svg>
  <svg class="arrow" style="left:1119px;top:2846px" viewBox="0 0 44 44"><circle cx="22" cy="22" r="20" fill="#fff" stroke="#1b6fb8" stroke-width="2.5"/><path d="M19 13L28 22L19 31" fill="none" stroke="#1b6fb8" stroke-width="2.5"/></svg>

  <article class="blog-card" style="left:140px">
    <div class="media" role="img" aria-label="Close-up of stacked washing machine doors" style="background:linear-gradient(135deg,#5c6470,#c9ced4 50%,#6b737d)"></div>
    <span class="blog-date">JAN 22, 2025</span>
    <h3>Lorem Ipsum is simply dummy text printing</h3>
    <div class="blog-rule"></div>
    <p>Lorem Ipsum is simply dummy text of the printing</p>
  </article>
  <article class="blog-card" style="left:456px">
    <div class="media" role="img" aria-label="Hand holding a glowing digital globe" style="background:linear-gradient(160deg,#0a1c3e,#1f5ea8 55%,#0d2146)"></div>
    <span class="blog-date">JAN 15, 2025</span>
    <h3>Lorem Ipsum is simply dummy text printing</h3>
    <div class="blog-rule"></div>
    <p>Lorem Ipsum is simply dummy text of the printing</p>
  </article>
  <article class="blog-card" style="left:773px">
    <div class="media" role="img" aria-label="Small dog wearing a teal collar outdoors" style="background:linear-gradient(135deg,#8a8a5a,#c98b4e 50%,#5b6b48)"></div>
    <span class="blog-date">DEC 10, 2024</span>
    <h3>Lorem Ipsum is simply dummy text printing</h3>
    <div class="blog-rule"></div>
    <p>Lorem Ipsum is simply dummy text of the printing</p>
  </article>

  <!-- Footer -->
  <footer class="site-footer">
    <div class="brand"><span class="brand-dot"></span>VORTEQ</div>
    <div class="footer-col" style="left:376px">
      <h4>MAIN LINKS</h4>
      <ul><li>Home</li><li>About Us</li><li>Services</li><li>Why choose Us</li><li>Contact Us</li></ul>
    </div>
    <div class="footer-col" style="left:602px">
      <h4>OTHER LINKS</h4>
      <ul style="margin-top:2px"><li>Terms and Conditions</li><li>Our Careers</li><li>Privacy Policy</li></ul>
    </div>
    <div class="footer-col" style="left:865px">
      <h4>NEWSLETTER</h4>
      <p class="newsletter-note">We Will Notify You Of Any Important News</p>
    </div>
    <div class="newsletter-field">Your Email Address
      <svg width="24" height="22" viewBox="0 0 24 22" fill="none" stroke="#1b6fb8" stroke-width="1.8" stroke-linejoin="round"><path d="M2 10L22 2L16 20L11 13Z"/><path d="M11 13L22 2"/></svg>
    </div>
    <div class="footer-rule"></div>
    <p class="copyright">© 2025 Vorteq I All Rights Reserved</p>
  </footer>

</div>
</body>
</html>
```